Business Card - connecting 2 souls and beggining the journey of self discovery

Logo on the front
with tag line

On the back list of services and contact details

Seminars
workshops
Coaching
podcasts

Darren Whitlow
Health & Wellbeing Life Coach
0491 372 615
darren@brightcoreliving.example
brightcoreliving.example

Industry/Entity Type

Life Coaching

Contact Information for Business Card

I like the use of colour from the logo to be used. I'm not a fan of white.

Requirements
Must have
• My tagline: The journey home starts with you
Nice to have
• Use of colour that is in the Brightcore Living logo

```html
<!DOCTYPE html>
<html lang="en">
<head>
<meta charset="utf-8">
<title>Darren Whitlow – Business Card</title>
<link href="https://fonts.googleapis.com/css2?family=Source+Sans+3:wght@400;600;700&family=Montserrat:wght@400&display=swap" rel="stylesheet">
<style>
  :root {
    --stage: #000000;
    --card: #2f3033;
    --divider: #45464a;
    --accent: #f3b51d;
    --mark: #f0745f;
    --ink: #ffffff;
    --muted: #8b8c90;
  }
  * { margin: 0; padding: 0; box-sizing: border-box; }
  html, body { width: 1200px; height: 900px; overflow: hidden; background: var(--stage); }
  body { position: relative; font-family: "Source Sans 3", "Myriad Pro", Arial, sans-serif; color: var(--ink); }

  .card {
    position: absolute;
    top: 271px;
    width: 457px;
    height: 281px;
    border-radius: 14px;
    background: var(--card);
  }
  .card--front { left: 137px; }
  .card--back { left: 626px; }

  /* brand lockup */
  .brand {
    position: absolute;
    display: flex;
    flex-direction: column;
    align-items: center;
    text-align: center;
  }
  .brand__dot { border-radius: 50%; background: var(--mark); }
  .brand__name { font-weight: 700; color: var(--ink); line-height: 1.15; }

  .card--front .brand { left: 44px; top: 70px; width: 124px; }
  .card--front .brand__dot { width: 64px; height: 64px; margin-bottom: 10px; }
  .card--front .brand__name { font-size: 16px; }

  .divider {
    position: absolute;
    left: 195px; top: 66px;
    width: 1px; height: 124px;
    background: var(--divider);
  }

  .identity { position: absolute; left: 222px; top: 64px; }
  .identity__name { font-size: 19px; font-weight: 700; color: var(--accent); line-height: 22px; }
  .identity__role { font-size: 13px; line-height: 18px; margin-top: 4px; }

  .contact { position: absolute; left: 222px; top: 131px; list-style: none; }
  .contact__item { display: flex; align-items: center; font-size: 13.5px; line-height: 19px; }
  .contact__icon { width: 10px; height: 10px; margin-right: 8px; fill: var(--accent); flex: none; }

  .services {
    position: absolute;
    left: 0; right: 0; top: 231px;
    display: flex; justify-content: center; align-items: center;
    list-style: none;
    font-size: 13.5px; font-weight: 600;
  }
  .services__item { display: flex; align-items: center; }
  .services__item + .services__item::before {
    content: "";
    width: 6px; height: 6px; border-radius: 50%;
    background: var(--accent);
    margin: 0 12px;
  }

  .card--back .brand { left: 0; right: 0; top: 74px; }
  .card--back .brand__dot { width: 62px; height: 62px; margin-bottom: 9px; }
  .card--back .brand__name { font-size: 16px; }

  .tagline {
    position: absolute;
    left: 0; right: 0; top: 185px;
    text-align: center;
    font-family: "Montserrat", "Gotham", Arial, sans-serif;
    font-size: 21px; font-weight: 400; letter-spacing: -0.6px;
    color: var(--muted);
  }
</style>
</head>
<body>

<section class="card card--front">
  <div class="brand">
    <span class="brand__dot"></span>
    <span class="brand__name">Brightcore Living</span>
  </div>

  <span class="divider"></span>

  <div class="identity">
    <h1 class="identity__name">Darren Whitlow</h1>
    <p class="identity__role">Health &amp; Wellbeing Life Coach</p>
  </div>

  <ul class="contact">
    <li class="contact__item">
      <svg class="contact__icon" viewBox="0 0 10 10" aria-hidden="true"><path d="M2 0.5 L3.6 2.6 L2.7 3.6 C3.3 5 4.7 6.4 6.2 7.2 L7.2 6.3 L9.5 7.9 L8.4 9.5 C4.5 9.4 0.6 5.5 0.5 1.6 Z"/></svg>
      0491 372 615
    </li>
    <li class="contact__item">
      <svg class="contact__icon" viewBox="0 0 10 10" aria-hidden="true"><path d="M0.5 2 H9.5 V8.5 H0.5 Z M1 2.5 L5 5.6 L9 2.5" stroke="#2f3033" stroke-width="0.8"/></svg>
      darren@brightcoreliving.example
    </li>
    <li class="contact__item">
      <svg class="contact__icon" viewBox="0 0 10 10" aria-hidden="true"><circle cx="5" cy="5" r="4.6"/><path d="M2.5 3 L4.5 3.5 L4 5.5 L5.5 7 L5 9 M7 1.8 L6.5 4 L8.5 5" stroke="#2f3033" stroke-width="0.8" fill="none"/></svg>
      www.brightcoreliving.example
    </li>
  </ul>

  <ul class="services">
    <li class="services__item">Seminars</li>
    <li class="services__item">Workshops</li>
    <li class="services__item">Coaching</li>
    <li class="services__item">Podcasts</li>
  </ul>
</section>

<section class="card card--back">
  <div class="brand">
    <span class="brand__dot"></span>
    <span class="brand__name">Brightcore Living</span>
  </div>
  <p class="tagline">The journey home starts with you</p>
</section>

</body>
</html>
```